Brake Test Training for Coal Mining

We offer Brake Test Training for Coal Mine workers. It's a legislative requirement that workers who are tasked with performing brake testing have certain competencies to do so. We test Light Vehicles and trailers, Heavy Vehicles and Mobile Mining Equipment like Graders, Scrapers and Dump Trucks.

```html
<!DOCTYPE html>
<html lang="en">
<head>
<meta charset="utf-8">
<title>Brake Test Training</title>
<link rel="stylesheet" href="https://fonts.googleapis.com/css2?family=Oswald:wght@700&family=Montserrat:wght@500;600;800&display=swap">
<style>
  :root {
    --navy: #1c2a63;
    --navy-deep: #15204f;
    --gold: #f6b213;
    --gold-dark: #c98a12;
    --white: #ffffff;
    --photo-a: #8a7a5c;
    --photo-b: #b9ad93;
  }
  * { margin: 0; padding: 0; box-sizing: border-box; }
  html, body { width: 1200px; height: 815px; overflow: hidden; background: var(--navy); }
  .billboard { position: relative; width: 1200px; height: 815px; background: var(--navy); overflow: hidden; font-family: "Montserrat", sans-serif; }
  .backdrop { position: absolute; inset: 0; }
  .brand-pill {
    position: absolute; left: 0; top: 40px; width: 400px; height: 140px;
    background: var(--white); border-radius: 0 70px 70px 0;
    display: flex; align-items: center; gap: 16px; padding-left: 36px;
  }
  .brand-dot { width: 54px; height: 54px; border-radius: 50%; background: var(--navy); flex: none; }
  .brand-name { font-family: "Montserrat", sans-serif; font-weight: 800; font-size: 25px; line-height: 1.15; color: var(--navy); text-transform: uppercase; }
  .headline {
    position: absolute; left: 580px; right: 40px; top: 22px;
    text-align: right; font-family: "Oswald", sans-serif; font-weight: 700;
    color: var(--gold); text-transform: uppercase; line-height: 1;
  }
  .headline .line-1 { display: block; font-size: 112px; letter-spacing: 1px; }
  .headline .line-2 { display: block; font-size: 128px; letter-spacing: 2px; margin-right: 60px; margin-top: -4px; }
  .services-intro { position: absolute; left: 530px; width: 630px; top: 312px; text-align: center; color: var(--white); font-weight: 500; font-size: 29px; line-height: 1.15; text-transform: uppercase; }
  .equipment-list { position: absolute; left: 440px; right: 40px; top: 470px; list-style: none; }
  .equipment-list li {
    height: 62px; margin-bottom: 12px; display: flex; align-items: center; justify-content: center;
    background: linear-gradient(90deg, rgba(246,178,19,0) 0%, var(--gold) 35%, var(--gold) 60%, #a9782f 100%);
    color: var(--navy-deep); font-weight: 800; font-size: 38px; text-transform: uppercase; letter-spacing: 0.5px; padding-left: 60px;
  }
  .contact-band {
    position: absolute; left: 0; right: 0; bottom: 0; height: 108px; background: var(--gold);
    display: flex; align-items: center; padding-left: 40px; gap: 20px;
    color: var(--navy); font-weight: 500; font-size: 28px;
  }
  .contact-item { display: flex; align-items: center; gap: 10px; white-space: nowrap; }
  .contact-item svg { width: 32px; height: 32px; flex: none; }
  .divider { width: 2px; height: 44px; background: var(--gold-dark); }
</style>
</head>
<body>
<main class="billboard">
  <svg class="backdrop" width="1200" height="815" viewBox="0 0 1200 815">
    <defs>
      <linearGradient id="photoTone" x1="0" y1="0" x2="1" y2="1">
        <stop offset="0" stop-color="var(--photo-b)"/>
        <stop offset="0.55" stop-color="var(--photo-a)"/>
        <stop offset="1" stop-color="#d9d6cf"/>
      </linearGradient>
    </defs>
    <polygon points="495,0 560,0 400,707 330,707" fill="var(--gold)"/>
    <polygon points="0,0 495,0 330,707 0,707" fill="url(#photoTone)" role="img" aria-label="Photo of a mining haul truck with a white service ute fitted with a crane"/>
  </svg>

  <div class="brand-pill">
    <span class="brand-dot"></span>
    <span class="brand-name">Ridgeline<br>Operator Skills</span>
  </div>

  <h1 class="headline"><span class="line-1">Brake Test</span><span class="line-2">Training</span></h1>

  <p class="services-intro">We test light vehicles &amp; trailers,<br>heavy vehicles &amp; mobile<br>mining equipment</p>

  <ul class="equipment-list">
    <li>Graders</li>
    <li>Scrapers</li>
    <li>Dump Trucks</li>
  </ul>

  <footer class="contact-band">
    <span class="contact-item">
      <svg viewBox="0 0 24 24"><path fill="var(--navy)" d="M6.6 10.8a15.1 15.1 0 0 0 6.6 6.6l2.2-2.2c.3-.3.7-.4 1-.2 1.1.4 2.3.6 3.6.6.6 0 1 .4 1 1V20c0 .6-.4 1-1 1A17 17 0 0 1 3 4c0-.6.4-1 1-1h3.5c.6 0 1 .4 1 1 0 1.3.2 2.5.6 3.6.1.3 0 .7-.2 1z"/></svg>
      1300 555 018
    </span>
    <span class="divider"></span>
    <span class="contact-item">
      <svg viewBox="0 0 24 24" fill="none" stroke="var(--navy)" stroke-width="1.8"><circle cx="12" cy="12" r="9.5"/><ellipse cx="12" cy="12" rx="4.2" ry="9.5"/><path d="M2.5 12h19M4 7h16M4 17h16"/></svg>
      www.ros.net.au
    </span>
    <span class="divider"></span>
    <span class="contact-item">
      <svg viewBox="0 0 24 24"><path fill="var(--navy)" d="M12 2a7 7 0 0 0-7 7c0 5.2 7 13 7 13s7-7.8 7-13a7 7 0 0 0-7-7zm0 9.5A2.5 2.5 0 1 1 12 6.5a2.5 2.5 0 0 1 0 5z"/></svg>
      24 Quarry St, Carrick. Qld 4725
    </span>
  </footer>
</main>
</body>
</html>
```